Tradeshow wall graphic featuring exhibitor branding

We are a software company representing the cruise industry. We are at a small trade show booth and need front and back artwork. We would like to include verbage from the attached word document. I have also included some past banners that we have used for reference. plinthwave.com

```html
<!DOCTYPE html>
<html lang="en">
<head>
<meta charset="utf-8">
<title>Plinthwave – Tradeshow Wall Graphic</title>
<link href="https://fonts.googleapis.com/css2?family=Montserrat:wght@700;800&family=Carlito&family=Lexend:wght@400&display=swap" rel="stylesheet">
<style>
  :root {
    --navy: #053d5f;
    --ink: #0c3a5a;
    --white: #ffffff;
    --sky-top: #f07a4e;
    --sky-pink: #d96b8c;
    --sky-violet: #6f5c9c;
    --sea-deep: #1b4b86;
    --sea-mid: #0f5282;
    --tab-light: #8ecbea;
    --tab-dark: #0a3d63;
  }
  * { margin: 0; padding: 0; box-sizing: border-box; }
  html, body { width: 827px; height: 1200px; overflow: hidden; background: #ffffff; }
  .poster {
    position: relative; width: 827px; height: 1200px; overflow: hidden;
    background: linear-gradient(180deg, var(--sky-top) 0%, var(--sky-pink) 12%, var(--sky-violet) 22%, var(--sea-deep) 38%, var(--sea-mid) 60%, #0e4a7c 100%);
  }
  .sunset-scene {
    position: absolute; left: 0; right: 0; top: 860px; bottom: 0;
    background: linear-gradient(180deg, #c9c4dc 0%, #f0b48a 30%, #e39a66 45%, #9db6c9 62%, #3f7fa0 80%, #2a6a8d 100%);
  }
  .brand-box {
    position: absolute; left: 85px; top: 0; width: 656px; height: 141px;
    background: var(--white); border-radius: 0 0 42px 42px;
    display: flex; align-items: center; justify-content: center;
  }
  .brand-name {
    font-family: 'Montserrat', sans-serif; font-weight: 800; font-size: 75px;
    color: var(--navy); letter-spacing: 0; line-height: 1; margin-top: 4px;
  }
  .headline {
    position: absolute; left: 0; right: 0; top: 186px; text-align: center;
    font-family: 'Montserrat', sans-serif; font-weight: 700; font-size: 66px;
    line-height: 72.5px; color: var(--white); letter-spacing: -0.5px;
    text-shadow: 2px 3px 5px rgba(0,0,0,0.35);
  }
  .subtitle {
    position: absolute; left: 0; right: 0; top: 511px; text-align: center;
    font-family: 'Carlito', sans-serif; font-size: 29px; color: var(--white);
  }
  .platform-tab {
    position: absolute; left: 107px; top: 595px; width: 613px; height: 66px;
    border-radius: 26px 26px 0 0;
    background: linear-gradient(180deg, var(--tab-light) 0%, #3d84b3 35%, var(--tab-dark) 100%);
    display: flex; align-items: center; justify-content: center;
  }
  .platform-tab span {
    font-family: 'Montserrat', sans-serif; font-weight: 800; font-size: 32px;
    color: var(--white); letter-spacing: 0.5px; text-shadow: 1px 2px 3px rgba(0,0,0,0.45);
  }
  .feature-panel {
    position: absolute; left: 76px; top: 661px; width: 675px; height: 320px;
    border-radius: 42px 42px 0 0;
    background: linear-gradient(180deg, var(--white) 0%, var(--white) 58%, rgba(255,255,255,0.6) 78%, rgba(255,255,255,0) 100%);
  }
  .feature-icon {
    position: absolute; fill: none; stroke: var(--ink); stroke-width: 1.6;
    stroke-linejoin: round; stroke-linecap: round;
  }
  .feature-label {
    position: absolute; white-space: nowrap; line-height: 26px;
    font-family: 'Lexend', sans-serif; font-size: 19.5px; color: var(--ink);
  }
</style>
</head>
<body>
<div class="poster">
  <div class="sunset-scene" role="img" aria-label="Photo of a large cruise ship sailing on calm sea at sunset, coastline on the left"></div>

  <div class="brand-box"><span class="brand-name">PLINTHWAVE</span></div>

  <h1 class="headline">BUILT FOR<br>CRUISE LINES &amp;<br>SHORE EXCURSION<br>OPERATORS</h1>

  <p class="subtitle">Control Cruise Inventory and Direct Bookings</p>

  <div class="platform-tab"><span>SEAMLESSLY ON ONE PLATFORM</span></div>

  <div class="feature-panel"></div>

  <!-- left column -->
  <svg class="feature-icon" style="left:119px; top:688px;" width="42" height="44" viewBox="0 0 42 44">
    <rect x="2" y="18" width="38" height="24"/><line x1="2" y1="30" x2="40" y2="30"/>
    <line x1="14" y1="18" x2="14" y2="42"/><line x1="27" y1="18" x2="27" y2="42"/>
    <polyline points="4,16 16,8 24,12 34,3"/><polyline points="29,3 34,3 34,8"/>
  </svg>
  <span class="feature-label" style="left:178px; top:705px;">Maximize Occupancy.</span>

  <svg class="feature-icon" style="left:111px; top:754px;" width="58" height="40" viewBox="0 0 58 40">
    <path d="M2 26 L56 22 L48 34 L8 34 Z"/><rect x="12" y="14" width="30" height="10"/>
    <rect x="20" y="6" width="14" height="8"/><line x1="17" y1="19" x2="37" y2="19"/>
    <circle cx="40" cy="30" r="5" fill="#ffffff"/><circle cx="40" cy="30" r="1.8"/>
  </svg>
  <span class="feature-label" style="left:178px; top:764px;">Control Cruise Inventory.</span>

  <svg class="feature-icon" style="left:116px; top:819px;" width="50" height="32" viewBox="0 0 50 32">
    <polyline points="2,2 8,2 12,22 34,22"/><path d="M9 7 H34 L32 17 H11"/>
    <circle cx="15" cy="27" r="3"/><circle cx="31" cy="27" r="3"/>
    <line x1="26" y1="12" x2="46" y2="12"/><polyline points="42,8 46,12 42,16"/>
  </svg>
  <span class="feature-label" style="left:178px; top:823px;">Manage Direct Sales.</span>

  <!-- right column -->
  <svg class="feature-icon" style="left:443px; top:700px;" width="56" height="30" viewBox="0 0 56 30">
    <rect x="14" y="2" width="26" height="20"/><path d="M40 8 H48 L54 16 V22 H40"/>
    <circle cx="20" cy="24" r="3.5" fill="#ffffff"/><circle cx="46" cy="24" r="3.5" fill="#ffffff"/>
    <line x1="2" y1="8" x2="10" y2="8"/><line x1="4" y1="13" x2="10" y2="13"/><line x1="6" y1="18" x2="10" y2="18"/>
    <path d="M28 5 L23 13 H28 L25 19"/>
  </svg>
  <span class="feature-label" style="left:514px; top:703px;">Power Daily Dispatch.</span>

  <svg class="feature-icon" style="left:452px; top:759px;" width="44" height="42" viewBox="0 0 44 42">
    <rect x="2" y="2" width="40" height="26"/><circle cx="22" cy="14" r="7"/>
    <path d="M20 10.5 L25 14 L20 17.5 Z"/>
    <circle cx="15" cy="30" r="3"/><circle cx="29" cy="30" r="3"/>
    <path d="M9 40 Q15 33 21 40"/><path d="M23 40 Q29 33 35 40"/>
  </svg>
  <span class="feature-label" style="left:514px; top:762px;">Live Demos at Wavefair</span>
</div>
</body>
</html>
```